Day Spa Web Design Project

We just created a blog to add to our main site. We need the colors to match our main site and the look and feel of the blog to be smoother and less ameture looking, like the examples below.

Main Site, match this color scheme:
http://www.verelladayspa.com/

The project site:
http://blog.verelladayspa.com/

Our industry leaders blog site is our comparative and examples of what we need:
http://blog.wellnooklist.com/
http://blog.purelathermjournal.com/
http://thekelotabathblog.com/ (i like the layout a lot)
http://www.kneadharbor.com/blog/

Requirements
Must have
• social sharing.
Responsive design (already has it just keep it)
appealing mobile front page

```html
<!DOCTYPE html>
<html lang="en">
<head>
<meta charset="utf-8">
<title>Verella Day Spa — Recent Blog</title>
<link href="https://fonts.googleapis.com/css2?family=Questrial&family=Tinos&family=Lato:wght@300;400;700&family=Arimo:wght@400&display=swap" rel="stylesheet">
<style>
:root{
  --page-top:#e2c08c;
  --page-mid:#f0d4a8;
  --page-bottom:#f2d3a6;
  --panel:#f6e1c1;
  --card:#faf0e3;
  --ink:#1c130b;
  --text:#5e4e3f;
  --head-black:#050302;
  --nav-top:#4a3a22;
  --nav-bottom:#1e160b;
  --nav-line:#6b5535;
  --button:#2b1d10;
  --white:#ffffff;
  --hero-a:#7d6650;
  --hero-b:#a8906f;
  --share-a:#7a6650;
  --share-b:#9c8466;
  --share-c:#b8a283;
}
*{box-sizing:border-box;margin:0;padding:0}
html,body{width:739px;height:1200px;overflow:hidden}
body{
  position:relative;
  background:linear-gradient(180deg,var(--page-top) 0,var(--page-mid) 120px,var(--page-bottom) 100%);
  font-family:"Lato",sans-serif;color:var(--text);
}
.site{position:absolute;left:44px;top:8px;width:651px;height:1112px;background:var(--panel)}
.masthead{height:78px;background:var(--head-black);border-radius:4px 4px 0 0;position:relative;color:var(--white)}
.brand{position:absolute;left:31px;top:22px;font-family:"Questrial",sans-serif}
.brand-name{font-size:26px;letter-spacing:.5px;line-height:1}
.brand-tag{font-size:10.5px;margin-top:3px;letter-spacing:.3px}
.call{position:absolute;right:20px;top:30px;text-align:right;font-family:"Lato",sans-serif}
.call-label{font-size:12px;font-weight:300}
.call-number{font-size:18.5px;letter-spacing:.5px;margin-top:1px}
.main-nav{height:34px;background:linear-gradient(180deg,var(--nav-top),var(--nav-bottom));display:flex;padding-left:10px}
.main-nav a{font-family:"Arimo",sans-serif;font-size:11px;color:var(--white);text-decoration:none;padding:0 10px;line-height:34px;border-right:1px solid var(--nav-line)}
.main-nav a:last-child{border-right:none}
.hero{position:absolute;left:12px;top:120px;width:630px;height:198px;border:2px solid #fbf2e3;
  background:linear-gradient(180deg,var(--hero-b),var(--hero-a))}
.section-title{position:absolute;left:19px;top:333px;font-family:"Lato",sans-serif;font-size:16px;font-weight:400;line-height:20px;color:var(--ink)}
.post{position:absolute;width:196px;background:var(--card);padding:11px 12px 0;border-bottom:4px solid var(--ink);box-shadow:0 0 3px rgba(120,80,30,.25)}
.post-photo{border:3px solid #fff;box-shadow:0 0 2px rgba(0,0,0,.15);margin-bottom:9px}
.post-title{font-family:"Tinos",serif;font-size:11px;font-weight:400;color:#2a1e12;margin-bottom:4px;letter-spacing:.2px}
.post-excerpt{font-size:7.6px;line-height:14.4px;font-weight:400;color:var(--text)}
.share{display:flex;gap:5px;align-items:center;margin-top:10px}
.share span{width:13px;height:13px;display:block;border-radius:2px}
.share .s1{background:var(--share-a)}.share .s2{background:var(--share-b)}.share .s3{background:var(--share-c)}
.share .count{width:17px;height:13px;border:1px solid #ddd;background:#fff;font-size:6px;line-height:11px;text-align:center;color:#333;border-radius:0;margin-left:2px}
.learn{display:inline-block;margin-top:10px;background:var(--button);color:var(--white);font-size:7.5px;padding:4px 10px;border-radius:2px;text-decoration:none}
.footer-nav{position:absolute;left:0;width:739px;top:1135px;text-align:center;font-size:8.5px;color:var(--ink)}
.footer-nav a{color:var(--ink);text-decoration:none}
.footer-nav .sep{margin:0 5px}
.copyright{position:absolute;top:1160px;left:0;width:739px;text-align:center;font-size:7.2px;color:#4c3d2e}
.social{position:absolute;top:1131px;left:632px;display:flex;gap:3px}
.social span{width:17px;height:17px;border-radius:50%;background:var(--ink);display:block}
</style>
</head>
<body>
<div class="site">
  <header class="masthead">
    <div class="brand">
      <div class="brand-name">Verella Day Spa</div>
      <div class="brand-tag">Natural Treatments for Body, Skin &amp; Nails</div>
    </div>
    <div class="call">
      <div class="call-label">Call Us Today</div>
      <div class="call-number">555.014.2290</div>
    </div>
  </header>
  <nav class="main-nav">
    <a href="#">Home</a><a href="#">Meet the Staff</a><a href="#">Press</a><a href="#">Tour Our Spa</a><a href="#">About</a><a href="#">Blog</a><a href="#">Specials</a><a href="#">Contact</a>
  </nav>
  <div class="hero" role="img" aria-label="Banner photo: candle in a bowl of spa stones with flowers"></div>
  <h2 class="section-title">Recent Blog</h2>

  <article class="post" style="left:16px;top:362px;height:290px">
    <div class="post-photo" role="img" aria-label="Woman relaxing during a back massage" style="height:99px;background:linear-gradient(120deg,#6a4a5a,#e8c8b0 55%,#f4efe9)"></div>
    <h3 class="post-title">BLOG HEADLINE HERE</h3>
    <p class="post-excerpt">Some stress is natural, but often times stress becomes a problem when it leaves you feeling overwhelmed and out of control. Seventy seven percent of Americans report experiencing physical symptoms of stress, according</p>
    <div class="share" style="margin-top:18px"><span class="s1"></span><span class="s2"></span><span class="s1"></span><span class="s3"></span><span class="s3"></span><span class="s2"></span><span class="count">1</span></div>
    <a class="learn" href="#">Learn More</a>
  </article>

  <article class="post" style="left:16px;top:662px;height:376px">
    <div class="post-photo" role="img" aria-label="Woman resting on a massage table" style="height:160px;background:linear-gradient(135deg,#a67a52,#e9c0a0 50%,#c79a70)"></div>
    <p class="post-excerpt">Mauris vel lacus vitae felis vestibulum volutpat. Etiam est nunc, venenatis in, tristique eu, imperdiet ac, nisl. Cum sociis natoque penatibus et magnis dis parturient montes, nascetur ridiculus mus. In iaculis facilisis massa. Etiam eu urna. Sed porta. Suspendisse quam leo, molestie sed, luctus quis, feugiat in, pede. Fusce tellus.</p>
    <div class="share"><span class="s1"></span><span class="s2"></span><span class="s1"></span><span class="s3"></span><span class="s3"></span><span class="s2"></span><span class="count">1</span></div>
    <a class="learn" href="#">Learn More</a>
  </article>

  <article class="post" style="left:226px;top:363px;height:243px">
    <div class="post-photo" role="img" aria-label="Woman relaxing with a towel and an orchid" style="height:99px;background:linear-gradient(90deg,#e8ebe2,#c9d6b8 50%,#7d9b5a)"></div>
    <h3 class="post-title">BLOG HEADLINE HERE</h3>
    <p class="post-excerpt">Have you been paying attention to the latest spring fashion trends? If not, don’t worry! We’ve got you covered from head to toe.</p>
    <div class="share"><span class="s1"></span><span class="s2"></span><span class="s1"></span><span class="s3"></span><span class="s3"></span><span class="s2"></span><span class="count">1</span></div>
    <a class="learn" href="#">Learn More</a>
  </article>

  <article class="post" style="left:226px;top:614px;height:240px">
    <div class="post-photo" role="img" aria-label="Three runway looks in bright spring colours" style="height:99px;background:linear-gradient(90deg,#e9824a,#f2d15c 30%,#d7b39a 55%,#3e6e78 70%,#e07ab8)"></div>
    <h3 class="post-title">BLOG HEADLINE HERE</h3>
    <p class="post-excerpt">unc tempus felis vitae urna. Vivamus porttitor, g, purus nisi eleifend libero, a tempus libero lectus feugiat felis.</p>
    <div class="share"><span class="s1"></span><span class="s2"></span><span class="s1"></span><span class="s3"></span><span class="s3"></span><span class="s2"></span><span class="count">1</span></div>
    <a class="learn" href="#">Learn More</a>
  </article>

  <article class="post" style="left:226px;top:862px;height:220px">
    <div class="post-photo" role="img" aria-label="Stacked black stones with a pink orchid and bamboo leaves" style="height:90px;background:linear-gradient(180deg,#a9cf7a,#eef3e2 55%,#c8c8c0)"></div>
    <h3 class="post-title">BLOG HEADLINE HERE</h3>
    <p class="post-excerpt">Spring fashion trends? If not, don’t worry! We’ve got you covered from head to toe.</p>
    <div class="share"><span class="s1"></span><span class="s2"></span><span class="s1"></span><span class="s3"></span><span class="s3"></span><span class="s2"></span><span class="count">1</span></div>
    <a class="learn" href="#">Learn More</a>
  </article>

  <article class="post" style="left:436px;top:364px;height:249px">
    <div class="post-photo" role="img" aria-label="Facial mask treatment being applied with a brush" style="height:99px;background:linear-gradient(120deg,#c89a80,#f3eee8 50%,#e6e1da)"></div>
    <h3 class="post-title">BLOG HEADLINE HERE</h3>
    <p class="post-excerpt">Some stress is natural, but often times stress becomes a problem when it leaves you feeling overwhelmed and out of control.</p>
    <div class="share"><span class="s1"></span><span class="s2"></span><span class="s1"></span><span class="s3"></span><span class="s3"></span><span class="s2"></span><span class="count">1</span></div>
    <a class="learn" href="#">Learn More</a>
  </article>

  <article class="post" style="left:434px;top:635px;height:301px">
    <div class="post-photo" role="img" aria-label="Relaxing facial massage with spa accessories" style="height:99px;background:linear-gradient(90deg,#e9c4a6,#f6eee6 55%,#a9845a)"></div>
    <h3 class="post-title">BLOG HEADLINE HERE</h3>
    <p class="post-excerpt">Some stress is natural, but often times stress becomes a problem when it leaves you feeling overwhelmed and out of control. Seventy seven percent of Americans report experiencing physical symptoms of stress, according to a 2012 study done by the National Calm Research Council.</p>
    <div class="share"><span class="s1"></span><span class="s2"></span><span class="s1"></span><span class="s3"></span><span class="s3"></span><span class="s2"></span><span class="count">1</span></div>
    <a class="learn" href="#">Learn More</a>
  </article>
</div>

<nav class="footer-nav">
  <a href="#">Home</a><span class="sep">|</span><a href="#">About Us</a><span class="sep">|</span><a href="#">Spa Services</a><span class="sep">|</span><a href="#">Spa Packages</a><span class="sep">|</span><a href="#">Specials</a><span class="sep">|</span><a href="#">Gift Certificates</a><span class="sep">|</span><a href="#">Spa Policy</a><span class="sep">|</span><a href="#">Contact Us</a>
</nav>
<div class="social" aria-label="Social links"><span></span><span></span><span></span></div>
<p class="copyright">© Copyright 2013 Verella Day Spa | 48 Linden Row, Marlow Bay, FL 30410</p>
</body>
</html>
```